Window Manufacturer: Pop-up wall display

We need a design for a window manufacturing company for our tradeshow% 26 # 39;% 26 # 39; wall% 26 # 39;% 26 # 39 ;. See below dimensions in the file named GT_3X3straightpopupLITE We want something that is not too complicated and we want a picture that will give the customers and distributors a look and feel of our company. We make windows and distribute patio doors and front doors.

Target Market(s)

Our distributors and our stores

Font styles to use
Other font styles liked:
• Nexa bold or Light

Colors
3377b5

Requirements
Must have
• Something clean and bold. I have pictures but cannot share on the site. Too big?
Nice to have
• Maybe we can play around with the logo icon ...
Should not have
• Do not play around with our squares to create the image and look.

```html
<!DOCTYPE html>
<html lang="en">
<head>
<meta charset="utf-8">
<title>Verrières Horizon – Pop-up Wall Display</title>
<link rel="stylesheet" href="https://fonts.googleapis.com/css2?family=Montserrat:wght@600;700&family=Roboto+Condensed:wght@700&display=swap">
<style>
  :root {
    --navy: #0b3a72;
    --navy-deep: #082d5a;
    --brand-blue: #3377b5;
    --sky: #1e9be0;
    --white: #ffffff;
    --mist: #e4e4e6;
    --ink: #111418;
    --kitchen-light: #f6efe0;
    --kitchen-warm: #d9b877;
    --kitchen-shadow: #8c7650;
  }
  html, body {
    margin: 0;
    padding: 0;
    width: 1200px;
    height: 1200px;
    overflow: hidden;
    background: var(--white);
  }
  .display-wall {
    position: relative;
    width: 1200px;
    height: 1200px;
    overflow: hidden;
  }
  .wall-graphics {
    position: absolute;
    inset: 0;
  }
  .brand {
    position: absolute;
    left: 205px;
    top: 35px;
    display: flex;
    align-items: center;
    gap: 36px;
  }
  .brand-square {
    width: 120px;
    height: 120px;
    border: 7px solid var(--white);
    box-sizing: border-box;
  }
  .brand-name {
    font-family: "Montserrat", sans-serif;
    font-weight: 600;
    font-size: 54px;
    letter-spacing: 3px;
    color: var(--white);
    line-height: 1;
  }
  .headline {
    position: absolute;
    left: 40px;
    top: 352px;
    width: 370px;
    margin: 0;
    font-family: "Roboto Condensed", sans-serif;
    font-weight: 700;
    font-size: 54px;
    line-height: 48px;
    text-align: center;
    text-transform: uppercase;
    color: var(--navy);
    letter-spacing: -0.5px;
  }
  .contact-phone {
    position: absolute;
    left: 95px;
    top: 1012px;
    display: flex;
    align-items: center;
    gap: 6px;
    font-family: "Montserrat", sans-serif;
    font-weight: 700;
    font-size: 36px;
    color: var(--navy);
  }
  .contact-phone svg { width: 28px; height: 28px; }
  .contact-web {
    position: absolute;
    left: 470px;
    top: 1060px;
    font-family: "Montserrat", sans-serif;
    font-weight: 600;
    font-size: 36px;
    color: var(--ink);
  }
</style>
</head>
<body>
<main class="display-wall">
  <svg class="wall-graphics" viewBox="0 0 1200 1200" width="1200" height="1200" xmlns="http://www.w3.org/2000/svg">
    <defs>
      <linearGradient id="kitchen-tone" x1="0" y1="0" x2="1" y2="0.3">
        <stop offset="0" stop-color="#ffffff"/>
        <stop offset="0.25" stop-color="var(--kitchen-light)"/>
        <stop offset="0.6" stop-color="var(--kitchen-warm)"/>
        <stop offset="1" stop-color="var(--kitchen-shadow)"/>
      </linearGradient>
      <linearGradient id="house-one" x1="0" y1="0" x2="0" y2="1">
        <stop offset="0" stop-color="#7aa6d6"/>
        <stop offset="0.55" stop-color="#d8d4cc"/>
        <stop offset="1" stop-color="#2f6f96"/>
      </linearGradient>
      <linearGradient id="house-two" x1="0" y1="0" x2="0" y2="1">
        <stop offset="0" stop-color="#8fb0d8"/>
        <stop offset="0.5" stop-color="#6e7886"/>
        <stop offset="1" stop-color="#4f8a3c"/>
      </linearGradient>
      <linearGradient id="house-three" x1="0" y1="0" x2="0" y2="1">
        <stop offset="0" stop-color="#86a8d4"/>
        <stop offset="0.55" stop-color="#6c7fa6"/>
        <stop offset="1" stop-color="#9a9a94"/>
      </linearGradient>
      <linearGradient id="mist-fade" x1="0" y1="0" x2="1" y2="0">
        <stop offset="0" stop-color="#f2f2f3"/>
        <stop offset="0.8" stop-color="var(--mist)"/>
        <stop offset="1" stop-color="#c9c9cc"/>
      </linearGradient>
    </defs>

    <!-- kitchen photo area -->
    <rect class="kitchen-photo" x="0" y="150" width="1200" height="800" fill="url(#kitchen-tone)" role="img" aria-label="Photo of a bright kitchen with a large white multi-pane window, glass-front cabinets and a marble island"/>

    <!-- light edge under the header band -->
    <path class="header-edge" d="M0,312 C260,240 520,205 760,222 C950,236 1100,300 1200,372 L1200,0 L0,0 Z" fill="#9db4cf"/>
    <!-- navy header band -->
    <path class="header-band" d="M0,296 C260,226 520,192 760,208 C950,222 1100,286 1200,356 L1200,0 L0,0 Z" fill="var(--navy)"/>

    <!-- bottom light band -->
    <path class="footer-band" d="M0,810 C200,860 420,930 640,930 C860,930 1050,870 1200,835 L1200,1200 L0,1200 Z" fill="url(#mist-fade)"/>

    <!-- project photo circles -->
    <circle cx="200" cy="828" r="104" fill="url(#house-one)" stroke="var(--white)" stroke-width="5" role="img" aria-label="Photo of a modern white two-storey house with large windows and a pool"/>
    <circle cx="484" cy="876" r="112" fill="url(#house-two)" stroke="var(--white)" stroke-width="5" role="img" aria-label="Photo of a contemporary house with glass garage doors at dusk"/>
    <circle cx="798" cy="866" r="120" fill="url(#house-three)" stroke="var(--white)" stroke-width="5" role="img" aria-label="Photo of a blue craftsman-style house with many lit windows"/>
  </svg>

  <header class="brand">
    <div class="brand-square"></div>
    <div class="brand-name">VERRIÈRES HORIZON</div>
  </header>

  <h1 class="headline">We make<br>windows and<br>distribute<br>patio doors<br>and<br>front doors</h1>

  <div class="contact-phone">
    <svg viewBox="0 0 24 24" aria-hidden="true">
      <circle cx="12" cy="12" r="12" fill="var(--sky)"/>
      <path d="M8.6 6.2l1.8 2.6-1.1 1.4c.7 1.6 2 2.9 3.6 3.6l1.4-1.1 2.6 1.8-.9 2.3c-4.6-.2-8.5-4.1-8.7-8.7z" fill="var(--white)"/>
    </svg>
    <span>555-210-4400</span>
  </div>

  <div class="contact-web">www.verrieres-horizon.com</div>
</main>
</body>
</html>
```